Investment Advisor E-Newsletter Banner Design

I need a banner designed for an email newsletter that will be sent monthly to clients and prospects. We want to see designs that are elegant and use our logo well. The banner should be 922x150px and should go well with the www.tlvbanda.com website. Should include Logo and email and phone number.

Target Market(s)

High net worth investors

Number of Pages Required

1 page

Requirements
Must have
• logo, place for email (info@tlvbanda.com) and phone number (415-297-6180), colors and design that work well with www.tlvbanda.com website

```html
<!DOCTYPE html>
<html lang="en">
<head>
<meta charset="utf-8">
<title>Tallvane Capital Advisory – Newsletter Banner</title>
<link rel="stylesheet" href="https://fonts.googleapis.com/css2?family=Montserrat:wght@500;600;700&display=swap">
<style>
  :root {
    --page-bg: #f2f2f2;
    --banner-bg: #eceef2;
    --brand-violet: #30248f;
    --brand-ink: #0e0e10;
    --brand-name: #2a2aa8;
    --text-dark: #111111;
    --text-light: #ffffff;
  }
  html, body {
    margin: 0;
    padding: 0;
    width: 1200px;
    height: 1200px;
    overflow: hidden;
    background: var(--page-bg);
  }
  .canvas {
    width: 1200px;
    height: 1200px;
    display: flex;
    align-items: center;
    justify-content: center;
  }
  .newsletter-banner {
    width: 1200px;
    height: 195px;
    display: block;
    font-family: "Montserrat", sans-serif;
  }
  .banner-base { fill: var(--banner-bg); }
  .curve-accent { fill: var(--brand-ink); }
  .contact-panel { fill: var(--brand-violet); }
  .brand-mark { fill: var(--brand-name); }
  .brand-name {
    fill: var(--brand-name);
    font-weight: 700;
    font-size: 15px;
  }
  .tagline {
    fill: var(--text-dark);
    font-weight: 700;
    font-size: 16.5px;
  }
  .email-pill { fill: var(--brand-ink); }
  .contact-text {
    fill: var(--text-light);
    font-weight: 600;
    font-size: 15.5px;
  }
  .contact-icon { fill: var(--text-light); }
</style>
</head>
<body>
  <main class="canvas">
    <svg class="newsletter-banner" viewBox="0 0 922 150" role="img" aria-label="Tallvane Capital Advisory newsletter banner">
      <rect class="banner-base" x="0" y="0" width="922" height="150"/>

      <!-- contact panel with curved edge -->
      <path class="curve-accent" d="M622 0 L922 0 L922 150 L548 150 C600 120 618 60 622 0 Z"/>
      <path class="contact-panel" d="M643 0 L922 0 L922 150 L560 150 C612 118 638 60 643 0 Z"/>

      <!-- brand -->
      <g class="brand">
        <rect class="brand-mark" x="34" y="64" width="20" height="20" rx="2"/>
        <text class="brand-name" x="62" y="72">Tallvane Capital</text>
        <text class="brand-name" x="62" y="90">Advisory</text>
      </g>

      <!-- tagline -->
      <text class="tagline" text-anchor="middle">
        <tspan x="406" y="68">Evidence-based Investment</tspan>
        <tspan x="406" y="89">Management. Personal Service.</tspan>
      </text>

      <!-- email -->
      <g class="contact-email">
        <rect class="email-pill" x="667" y="41" width="213" height="36" rx="18"/>
        <g class="contact-icon">
          <path d="M685 53 h14 v11 h-14 Z" />
          <path d="M685 53 L692 59 L699 53" fill="none" stroke="#0e0e10" stroke-width="1.4"/>
        </g>
        <text class="contact-text" x="708" y="64.5">info@tlvbanda.com</text>
      </g>

      <!-- phone -->
      <g class="contact-phone">
        <path class="contact-icon" d="M712 97 c1-1 2-1 3 0 l2 2 c1 1 1 2 0 3 l-1 1 c1 2 3 4 5 5 l1-1 c1-1 2-1 3 0 l2 2 c1 1 1 2 0 3 l-1 1 c-2 2-6 0-9-3 s-5-7-3-9 Z"/>
        <text class="contact-text" x="734" y="109">415-297-6180</text>
      </g>
    </svg>
  </main>
</body>
</html>
```